Request for Business Card Design

Hi. My name is Marlene, I am looking for a new business card design for my company, Quarrow Signal Instruments, LLC. I really like the design you did for Tarsel Venture and was hoping you could do something similar using our full logo and our mark. I am also open to any raised texture design using our mark. I have attached our full logo, which would need to be somewhere on the card, as well as the mark in both outline and full form, as well as our brand colors / guide. The card does not have to be white, as long as our logo and mark appear. I actually like darker colored business cards more, but am open to all options. If you are interested in working with me, please let me know. We would also take the business card design into letterhead design if you can do that.

```html
<!DOCTYPE html>
<html lang="en">
<head>
<meta charset="utf-8">
<title>Quarrow Signal Instruments — Business Card</title>
<link href="https://fonts.googleapis.com/css2?family=Barlow:wght@400;500;600&family=Montserrat:wght@800&display=swap" rel="stylesheet">
<style>
  :root {
    --bg-light: #ececec;
    --bg-dark: #8a8a8a;
    --card-dark: #1f1d1e;
    --card-mid: #3a393a;
    --brand-blue: #1a8fb3;
    --brand-blue-light: #3aa8c9;
    --text-white: #f4f4f4;
    --text-grey: #55585a;
    --notch-grey: #3d3d3e;
  }
  * { box-sizing: border-box; margin: 0; padding: 0; }
  html, body { width: 1200px; height: 1200px; overflow: hidden; }
  body {
    background: linear-gradient(120deg, var(--bg-light) 0%, #c9c9c9 55%, var(--bg-dark) 100%);
    font-family: "Barlow", sans-serif;
    position: relative;
  }
  .card {
    position: absolute;
    left: 250px;
    width: 700px;
    height: 400px;
    border-radius: 24px;
    overflow: hidden;
    box-shadow: 0 14px 30px rgba(0,0,0,0.28);
  }
  /* Front */
  .card-front { top: 150px; background: var(--card-dark); }
  .front-texture {
    position: absolute; inset: 0;
    background: radial-gradient(ellipse at 40% 30%, #4a494a 0%, var(--card-mid) 35%, var(--card-dark) 100%);
  }
  .front-lockup {
    position: absolute; left: 0; right: 0; top: 176px;
    display: flex; align-items: center; justify-content: center; gap: 16px;
  }
  .front-lockup .lockup-dot {
    width: 40px; height: 40px; border-radius: 50%; background: var(--text-white);
  }
  .front-lockup .lockup-name {
    color: var(--text-white); font-weight: 600; font-size: 34px;
    letter-spacing: 3px; text-transform: uppercase;
  }
  /* Back */
  .card-back {
    top: 650px;
    background: linear-gradient(110deg, #3b3a3b 0%, var(--card-dark) 45%, #1a191a 100%);
  }
  .edge-band { position: absolute; right: 0; width: 16px; background: var(--brand-blue); }
  .edge-band.top { top: 0; height: 150px; border-bottom-left-radius: 8px; }
  .edge-band.bottom { bottom: 0; height: 150px; border-top-left-radius: 8px; }
  .edge-notch {
    position: absolute; right: 0; top: 170px; width: 14px; height: 60px;
    background: var(--notch-grey); border-radius: 6px 0 0 6px;
  }
  .back-lockup {
    position: absolute; left: 56px; top: 48px;
    display: flex; align-items: center; gap: 16px;
  }
  .back-lockup .lockup-dot {
    width: 58px; height: 58px; border-radius: 50%; background: var(--brand-blue-light);
  }
  .back-lockup .lockup-name {
    color: var(--text-grey); font-weight: 600; font-size: 27px;
    letter-spacing: 2.5px; text-transform: uppercase;
  }
  .person { position: absolute; right: 56px; top: 140px; text-align: right; }
  .person-name {
    font-family: "Montserrat", sans-serif; font-weight: 800;
    color: var(--brand-blue); font-size: 30px;
  }
  .person-role { color: var(--text-white); font-size: 19px; letter-spacing: 1.5px; margin-top: 4px; }
  .address {
    position: absolute; left: 56px; top: 212px;
    color: var(--text-white); font-size: 19px; line-height: 24px; letter-spacing: 1.2px;
  }
  .contact-list {
    position: absolute; left: 56px; top: 270px; list-style: none;
    color: var(--text-white); font-size: 19px; line-height: 26px; letter-spacing: 1.2px;
  }
  .contact-list li { display: flex; align-items: center; gap: 12px; }
  .contact-list svg { width: 16px; height: 16px; fill: var(--brand-blue); flex: none; }
</style>
</head>
<body>

<section class="card card-front" aria-label="Card front">
  <div class="front-texture" role="img" aria-label="Raised gloss texture of repeated brand marks across the dark card"></div>
  <div class="front-lockup">
    <span class="lockup-dot"></span>
    <span class="lockup-name">Quarrow Signal Instruments</span>
  </div>
</section>

<section class="card card-back" aria-label="Card back">
  <div class="edge-band top"></div>
  <div class="edge-notch"></div>
  <div class="edge-band bottom"></div>

  <div class="back-lockup">
    <span class="lockup-dot"></span>
    <span class="lockup-name">Quarrow Signal Instruments</span>
  </div>

  <div class="person">
    <p class="person-name">Marlene</p>
    <p class="person-role">Founder &amp; Director</p>
  </div>

  <p class="address">1180 Ridgeview Parkway.<br>Loveland, CO 80538</p>

  <ul class="contact-list">
    <li>
      <svg viewBox="0 0 16 16" aria-hidden="true"><path d="M3.5 1.5l2.5 0 1 3.5-1.6 1.2a8 8 0 0 0 4.4 4.4L11 9l3.5 1v2.5A2 2 0 0 1 12.5 14.5 11 11 0 0 1 1.5 3.5 2 2 0 0 1 3.5 1.5z"/></svg>
      +001 970 555 0142
    </li>
    <li>
      <svg viewBox="0 0 16 16" aria-hidden="true"><path d="M4 1h8v4H4z M1 6h14v6h-3v3H4v-3H1z M5.5 10v3.5h5V10z"/></svg>
      +001 970 555 0187
    </li>
    <li>
      <svg viewBox="0 0 16 16" aria-hidden="true"><path d="M1 3h14v10H1z M1.5 3.5L8 9l6.5-5.5v1L8 10 1.5 4.5z" fill-rule="evenodd"/></svg>
      info@quarrowsignal.com
    </li>
    <li>
      <svg viewBox="0 0 16 16" aria-hidden="true"><path d="M8 1a7 7 0 1 0 0 14A7 7 0 0 0 8 1zm0 1.5c.9 0 1.9 1.6 2.2 4.5H5.8C6.1 4.1 7.1 2.5 8 2.5zM2.6 7h1.9c0-1.6.4-3 .9-4A5.5 5.5 0 0 0 2.6 7zm0 2a5.5 5.5 0 0 0 2.8 4c-.5-1-.9-2.4-.9-4zm3.2 0c.3 2.9 1.3 4.5 2.2 4.5s1.9-1.6 2.2-4.5zm5.7 0c0 1.6-.4 3-.9 4a5.5 5.5 0 0 0 2.8-4zm1.9-2a5.5 5.5 0 0 0-2.8-4c.5 1 .9 2.4.9 4z"/></svg>
      www.quarrowsignal.com
    </li>
  </ul>
</section>

</body>
</html>
```